Plumbing & Heating company

A leaflet containing -

Company name - Larkfield Plumbing Solutions
logo
Mobile number - 07700 914062
Landline - 01632 870215
Email - Info@larkfieldplumbing.example
website - Larkfield-plumbing.example
Social media logos - insta, Facebook

services we offer

- Boiler replacements (free quote)
- General plumbing & heating
- Tap replacements
- 1st & 2nd
- New builds & Extensions
- Cylinder replcemets

```html
<!DOCTYPE html>
<html lang="en">
<head>
<meta charset="utf-8">
<title>Larkfield Plumbing Solutions – Services</title>
<link rel="stylesheet" href="https://fonts.googleapis.com/css2?family=Archivo:wght@800;900&family=Source+Sans+3:wght@400;600;700&display=swap">
<style>
  :root {
    --brand-blue: #0b4f96;
    --brand-blue-light: #2a9ad6;
    --brand-red: #e8343b;
    --brand-orange: #f07a1f;
    --ink: #1d1d1f;
    --white: #ffffff;
    --photo-light: #e9eaec;
    --photo-mid: #c9ccd0;
    --copper: #b8743f;
    --wood: #b7875a;
  }
  * { margin: 0; padding: 0; box-sizing: border-box; }
  html, body { width: 857px; height: 1200px; overflow: hidden; background: var(--white); }
  .leaflet {
    position: relative; width: 857px; height: 1200px; overflow: hidden;
    background: var(--white);
    font-family: "Source Sans 3", "Helvetica Neue", Arial, sans-serif;
    color: var(--ink);
  }
  .hero { position: absolute; inset: 0; width: 857px; height: 1200px; }

  .services-title {
    position: absolute; left: 52px; top: 648px;
    font-family: "Archivo", Arial, sans-serif; font-weight: 900;
    line-height: 1; letter-spacing: -0.5px;
  }
  .services-title .line-red { display: block; color: var(--brand-red); font-size: 55px; }
  .services-title .line-blue { display: block; color: var(--brand-blue); font-size: 60px; margin-top: 2px; }

  .service-list { position: absolute; left: 53px; top: 776px; list-style: none; }
  .service-list li {
    display: flex; align-items: center; height: 35.8px;
    font-size: 24px; color: var(--ink);
  }
  .service-list li strong { font-weight: 700; margin-left: 6px; }
  .service-list svg { width: 22px; height: 22px; margin-right: 12px; flex: none; }

  .brand {
    position: absolute; left: 410px; top: 800px; width: 400px;
    display: flex; flex-direction: column; align-items: center; text-align: center;
    color: var(--brand-blue); font-family: "Archivo", Arial, sans-serif; font-weight: 800;
  }
  .brand-mark { width: 54px; height: 54px; border-radius: 50%; background: var(--brand-orange); margin-bottom: 12px; }
  .brand-name { font-size: 44px; line-height: 1.05; text-transform: uppercase; }
  .brand-sub { font-size: 21px; letter-spacing: 2px; text-transform: uppercase; margin-top: 4px; }

  .contact-bar {
    position: absolute; left: 45px; top: 1025px; width: 767px; height: 32px;
    background: var(--brand-blue);
    color: var(--white); font-family: "Archivo", Arial, sans-serif; font-weight: 800;
    font-size: 20px; letter-spacing: 1px; line-height: 32px; padding-left: 17px;
  }
  .contact-item {
    position: absolute; display: flex; align-items: center;
    font-size: 21px; color: var(--ink); height: 26px;
  }
  .contact-item svg { width: 21px; height: 21px; margin-right: 12px; flex: none; }
  .contact-mobile { left: 58px; top: 1075px; }
  .contact-landline { left: 58px; top: 1106px; }
  .contact-email { left: 271px; top: 1075px; }
  .contact-web { left: 271px; top: 1106px; }
  .contact-email svg, .contact-web svg { margin-right: 17px; }

  .social { position: absolute; left: 716px; top: 1092px; display: flex; gap: 12px; }
  .social span { width: 36px; height: 36px; border-radius: 50%; display: block; }
  .social .social-one { background: var(--brand-red); }
  .social .social-two { background: var(--brand-blue); }

  .footer-band {
    position: absolute; left: 0; top: 1169px; width: 857px; height: 31px;
    background: linear-gradient(90deg, var(--brand-blue), var(--brand-blue-light));
  }
</style>
</head>
<body>
<main class="leaflet">
  <svg class="hero" viewBox="0 0 857 1200" aria-hidden="false">
    <defs>
      <linearGradient id="mainPhotoTone" x1="0" y1="0" x2="1" y2="1">
        <stop offset="0" stop-color="#f1f2f3"/>
        <stop offset="0.55" stop-color="#dcdee1"/>
        <stop offset="1" stop-color="#c49066"/>
      </linearGradient>
      <linearGradient id="boilerPhotoTone" x1="0" y1="0" x2="1" y2="1">
        <stop offset="0" stop-color="#c69b6c"/>
        <stop offset="1" stop-color="#a97a4f"/>
      </linearGradient>
      <linearGradient id="pipeworkPhotoTone" x1="0" y1="0" x2="1" y2="1">
        <stop offset="0" stop-color="#8d7a66"/>
        <stop offset="1" stop-color="#c07b4a"/>
      </linearGradient>
      <linearGradient id="waveBlue" x1="0" y1="0" x2="1" y2="0">
        <stop offset="0" stop-color="#0b4f96"/>
        <stop offset="1" stop-color="#2a9ad6"/>
      </linearGradient>
    </defs>

    <rect class="main-photo" x="0" y="0" width="857" height="720" fill="url(#mainPhotoTone)"
          role="img" aria-label="Photo of a finished cylinder and boiler installation with neat copper pipework and valves"/>

    <path class="wave-band" fill="url(#waveBlue)"
          d="M0,398 C60,386 100,384 150,380 L300,530 C420,608 600,625 857,645 L857,1200 L0,1200 Z"/>
    <path class="wave-white" fill="#ffffff"
          d="M0,467 C50,452 90,448 120,446 L300,575 C380,640 500,690 620,700 C720,708 800,710 857,718 L857,1200 L0,1200 Z"/>

    <circle cx="197" cy="232" r="143" fill="#ffffff"/>
    <circle cx="197" cy="232" r="129" fill="url(#boilerPhotoTone)"
            role="img" aria-label="Photo of a wall-mounted boiler with copper pipework on a timber board"/>
    <circle cx="197" cy="470" r="143" fill="#ffffff"/>
    <circle cx="197" cy="470" r="129" fill="url(#pipeworkPhotoTone)"
            role="img" aria-label="Photo of first-fix copper pipe runs between timber joists"/>
  </svg>

  <h1 class="services-title">
    <span class="line-red">SERVICES</span>
    <span class="line-blue">WE OFFER</span>
  </h1>

  <ul class="service-list">
    <li><svg viewBox="0 0 24 24"><path d="M2 13 L9 20 L22 4" fill="none" stroke="#0b4f96" stroke-width="4" stroke-linecap="round" stroke-linejoin="round"/></svg>Boiler replacements<strong>(free quote)</strong></li>
    <li><svg viewBox="0 0 24 24"><path d="M2 13 L9 20 L22 4" fill="none" stroke="#e8343b" stroke-width="4" stroke-linecap="round" stroke-linejoin="round"/></svg>General plumbing &amp; heating</li>
    <li><svg viewBox="0 0 24 24"><path d="M2 13 L9 20 L22 4" fill="none" stroke="#0b4f96" stroke-width="4" stroke-linecap="round" stroke-linejoin="round"/></svg>Tap replacements</li>
    <li><svg viewBox="0 0 24 24"><path d="M2 13 L9 20 L22 4" fill="none" stroke="#e8343b" stroke-width="4" stroke-linecap="round" stroke-linejoin="round"/></svg>1st &amp; 2nd</li>
    <li><svg viewBox="0 0 24 24"><path d="M2 13 L9 20 L22 4" fill="none" stroke="#0b4f96" stroke-width="4" stroke-linecap="round" stroke-linejoin="round"/></svg>New builds &amp; Extensions</li>
    <li><svg viewBox="0 0 24 24"><path d="M2 13 L9 20 L22 4" fill="none" stroke="#e8343b" stroke-width="4" stroke-linecap="round" stroke-linejoin="round"/></svg>Cylinder replacements</li>
  </ul>

  <div class="brand">
    <span class="brand-mark" aria-hidden="true"></span>
    <span class="brand-name">Larkfield</span>
    <span class="brand-sub">Plumbing Solutions</span>
  </div>

  <div class="contact-bar">GET IN TOUCH</div>

  <div class="contact-item contact-mobile">
    <svg viewBox="0 0 24 24"><path d="M6.6 10.8c1.4 2.8 3.8 5.1 6.6 6.6l2.2-2.2c.3-.3.7-.4 1-.2 1.1.4 2.3.6 3.6.6.6 0 1 .4 1 1V20c0 .6-.4 1-1 1C10.6 21 3 13.4 3 4c0-.6.4-1 1-1h3.5c.6 0 1 .4 1 1 0 1.3.2 2.5.6 3.6.1.3 0 .7-.2 1z" fill="#e8343b"/></svg>
    07700 914062
  </div>
  <div class="contact-item contact-landline">
    <svg viewBox="0 0 24 24"><path d="M2 9c0-2 4.5-4 10-4s10 2 10 4v2h-5V9.5c-1.5-.5-3.2-.7-5-.7s-3.5.2-5 .7V11H2z M5 13h14l2 7H3z" fill="#0b4f96"/></svg>
    01632 870215
  </div>
  <div class="contact-item contact-email">
    <svg viewBox="0 0 24 24"><rect x="2" y="5" width="20" height="14" fill="none" stroke="#0b4f96" stroke-width="2"/><path d="M2 5 L12 13 L22 5 M2 19 L9 12 M22 19 L15 12" fill="none" stroke="#0b4f96" stroke-width="2"/></svg>
    Info@larkfieldplumbing.example
  </div>
  <div class="contact-item contact-web">
    <svg viewBox="0 0 24 24"><g fill="none" stroke="#e8343b" stroke-width="1.8"><circle cx="12" cy="12" r="10"/><ellipse cx="12" cy="12" rx="4.5" ry="10"/><path d="M2 12h20M4 7h16M4 17h16"/></g></svg>
    Larkfield-plumbing.example
  </div>

  <div class="social" aria-label="Social media">
    <span class="social-one"></span>
    <span class="social-two"></span>
  </div>

  <div class="footer-band"></div>
</main>
</body>
</html>
```